Real Estate Webpage Design

We have an existing website: ferndaleestatecollective.com.au
We focus customised service mainly on Property Management and second-hand property sales.
We are not entirely happy about the current design and layout can stay roughly the same as the back end coding is linked to a CRM system.
We would like to see the design are more reachable to our clients and appearing.
Please check our Website Design Draft for more details.

Industry/Entity Type

Real estate Agency

Number of Pages Required

5+ page

Font styles to use
Sans Serif

Colors

Designer to choose colors to be used in the design.

```html
<!DOCTYPE html>
<html lang="en">
<head>
<meta charset="utf-8">
<title>Ferndale Estate Collective</title>
<link href="https://fonts.googleapis.com/css2?family=Raleway:wght@400;500;600;700&family=Arimo:ital,wght@0,400;0,700;1,400&display=swap" rel="stylesheet">
<style>
:root{
  --gold:#e3b345;
  --gold-dark:#d6a535;
  --navy:#1b2538;
  --ink:#222;
  --grey:#555;
  --line:#e4e4e4;
  --white:#fff;
}
*{box-sizing:border-box;margin:0;padding:0}
html,body{width:1200px;height:4438px;overflow:hidden}
body{position:relative;background:var(--white);font-family:"Arimo",Arial,sans-serif;color:var(--ink)}
.abs{position:absolute}

/* top bar */
.topbar{left:0;top:0;width:1200px;height:50px;background:var(--gold);color:var(--white);font-size:13px}
.topbar .social{position:absolute;left:112px;top:11px;display:flex;gap:8px}
.topbar .social span{width:28px;height:28px;border:1.5px solid var(--white);border-radius:50%}
.topbar .contact{position:absolute;right:112px;top:17px;display:flex;gap:30px}

/* nav */
.nav{left:0;top:50px;width:1200px;height:100px;background:var(--white)}
.brand{position:absolute;display:flex;align-items:center;gap:10px;font-family:"Raleway",sans-serif;font-weight:700;color:var(--gold)}
.brand i{display:block;background:var(--gold)}
.nav .brand{left:112px;top:25px;font-size:36px}
.nav .brand i{width:34px;height:34px}
.nav ul{position:absolute;left:460px;top:44px;list-style:none;display:flex;gap:32px;font-family:"Raleway",sans-serif;font-size:15px;font-weight:500}
.nav li.active{color:var(--gold)}
.nav .dot{position:absolute;left:471px;top:20px;width:18px;height:18px;border:2px solid var(--gold);border-radius:3px}

/* hero */
.hero{left:0;top:150px;width:1200px;height:690px}
.hero-photo{position:absolute;inset:0;background:linear-gradient(180deg,#9aa8a2 0%,#6f6a5c 35%,#3f3a32 70%,#2b2f33 100%)}
.hero-box{position:absolute;left:285px;top:195px;width:630px;height:300px;background:rgba(35,30,25,.72);text-align:center}
.hero-box h1{font-family:"Raleway",sans-serif;font-weight:500;font-size:50px;line-height:66px;color:var(--white);margin-top:50px;white-space:nowrap}
.hero-box h1 span{display:block;color:var(--gold)}
.btn-gold{position:absolute;background:var(--gold);color:var(--white);border-radius:32px;font-family:"Raleway",sans-serif;font-size:20px;text-align:center}
.hero .btn-gold{left:498px;top:403px;width:204px;height:63px;line-height:63px}
.dots{left:574px;top:827px;display:flex;gap:6px}
.dots span{width:13px;height:13px;border-radius:50%;background:#ddd}
.dots span.on{background:var(--gold)}

/* welcome */
.welcome{left:0;top:915px;width:1200px;text-align:center}
.welcome h2{font-family:"Raleway",sans-serif;font-weight:500;font-size:27px}
.welcome h3{font-family:"Raleway",sans-serif;font-weight:500;font-size:38px;color:var(--gold);margin-top:6px}
.welcome p{font-size:13px;line-height:26px;color:var(--grey);width:740px;margin:22px auto 0}
.service{position:absolute;border-radius:50%;background:var(--white);box-shadow:0 0 0 4px #f0f0f0;text-align:center;color:var(--ink)}
.service h4{font-family:"Raleway",sans-serif;font-weight:600;font-size:19px;margin-top:10px}
.service p{font-size:13px;line-height:26px;color:var(--grey);margin-top:10px}
.service svg{margin-top:40px}
.service.main{background:var(--gold);color:var(--white);box-shadow:none}
.service.main p{color:var(--white)}

/* about */
.about{left:0;top:1560px;width:1200px;height:655px;background:var(--gold)}
.about-photo{position:absolute;left:160px;top:178px;width:422px;height:417px;background:linear-gradient(135deg,#e8e4dc,#a9a196 60%,#5c5a55)}
.about h2{position:absolute;left:668px;top:165px;font-family:"Raleway",sans-serif;font-weight:500;font-size:35px;color:var(--white)}
.about p{position:absolute;left:673px;width:386px;font-size:13px;line-height:26px;color:var(--white);text-align:justify}
.btn-line{position:absolute;left:673px;top:525px;width:164px;height:50px;line-height:48px;border:1.5px solid var(--white);border-radius:26px;color:var(--white);text-align:center;font-family:"Raleway",sans-serif;font-size:16px}

/* listings */
.listings-title{left:0;top:2268px;width:1200px;text-align:center;font-family:"Raleway",sans-serif;font-weight:500;font-size:32px}
.tabs{left:289px;top:2336px;display:flex;gap:18px}
.tabs span{width:110px;height:40px;line-height:38px;border:1.5px solid #999;border-radius:20px;text-align:center;font-size:13px}
.tabs span.on{border-color:var(--gold);color:var(--gold)}
.card{position:absolute;top:2425px;width:311px;height:580px;background:var(--white);box-shadow:0 0 0 1px var(--line)}
.card .photo{height:256px}
.card h5{text-align:center;font-family:"Raleway",sans-serif;font-weight:500;font-size:20px;color:var(--gold);margin-top:22px}
.card .addr{text-align:center;font-size:13px;color:var(--grey);margin-top:8px}
.card dl{display:grid;grid-template-columns:142px 1fr;margin:22px 0 0 25px;font-size:13px;line-height:29px;color:var(--grey)}
.card .cta{position:absolute;left:0;bottom:0;width:100%;height:54px;line-height:54px;background:var(--navy);color:var(--white);text-align:center;font-family:"Raleway",sans-serif;font-size:19px}
.card .cta.gold{background:var(--gold)}

/* video */
.video{left:0;top:3083px;width:1200px;height:512px;background:linear-gradient(180deg,#1c2332 0%,#4a4c52 45%,#2a2d33 100%)}
.video .play{position:absolute;left:548px;top:155px;width:104px;height:104px;border:3px solid var(--white);border-radius:50%}
.video h2{position:absolute;left:0;top:285px;width:1200px;text-align:center;font-family:"Raleway",sans-serif;font-weight:500;font-size:50px;color:var(--white)}

/* testimonials */
.testi-title{left:0;top:3638px;width:1200px;text-align:center;font-family:"Raleway",sans-serif;font-weight:600;font-size:36px}
.testi-rule{left:570px;top:3698px;width:60px;height:3px;background:var(--gold)}
.testi{position:absolute;top:3745px;width:474px;height:253px;background:var(--white);box-shadow:0 0 0 2px #eef0f3}
.testi .avatar{position:absolute;left:30px;top:22px;width:104px;height:104px;border-radius:50%;background:linear-gradient(160deg,#c9a68a,#6b4d3a)}
.testi .name{position:absolute;left:160px;top:45px;font-family:"Raleway",sans-serif;font-weight:500;font-size:17px}
.testi .role{position:absolute;left:160px;top:72px;font-size:12px;color:var(--grey)}
.testi .stars{position:absolute;left:160px;top:90px;color:var(--gold);font-size:13px;letter-spacing:1px}
.testi .quote{position:absolute;right:30px;top:20px;font-family:"Raleway",sans-serif;font-size:130px;line-height:130px;color:#e6e6e6;font-weight:700}
.testi p{position:absolute;left:35px;top:155px;width:410px;font-size:13px;font-style:italic;line-height:26px;color:var(--grey)}

/* footer */
.footer{left:0;top:4070px;width:1200px;height:368px}
.footer .brand{left:442px;top:100px;font-size:54px}
.footer .brand i{width:46px;height:46px}
.footer ul{position:absolute;left:0;top:188px;width:1200px;list-style:none;display:flex;justify-content:center;gap:32px;color:var(--white);font-family:"Raleway",sans-serif;font-size:15px}
.footer .social{position:absolute;left:498px;top:240px;display:flex;gap:8px}
.footer .social span{width:44px;height:44px;border:2px solid var(--gold);border-radius:50%}
.footer .copy{position:absolute;left:0;top:313px;width:1200px;text-align:center;color:var(--white);font-size:14px}
</style>
</head>
<body>

<header class="abs topbar">
  <div class="social"><span></span><span></span><span></span><span></span></div>
  <div class="contact"><span>&#9742; Call Us : 02 5550 1234</span><span>&#9993; Email : hello@ferndaleestate.com.au</span></div>
</header>

<nav class="abs nav">
  <div class="brand"><i></i>Ferndale</div>
  <div class="dot"></div>
  <ul>
    <li class="active">Home</li><li>About Us</li><li>Leasing</li><li>Buy</li><li>Sell</li><li>Our Team</li><li>Blog</li><li>Contact Us</li>
  </ul>
</nav>

<section class="abs hero">
  <div class="hero-photo" role="img" aria-label="Modern two-storey home with pool terrace at dusk"></div>
  <svg class="abs" style="left:0;top:620px" width="1200" height="70" viewBox="0 0 1200 70">
    <polygon points="0,0 600,45 1200,0 1200,70 0,70" fill="#fff"/>
    <polyline points="0,0 600,45 1200,0" fill="none" stroke="#e3b345" stroke-width="5"/>
  </svg>
  <div class="hero-box">
    <h1>FERNDALE<span>ESTATE COLLECTIVE</span></h1>
  </div>
  <div class="btn-gold">GET IN TOUCH</div>
</section>
<div class="abs dots"><span></span><span class="on"></span><span></span></div>

<section class="abs welcome">
  <h2>Welcome to</h2>
  <h3>Ferndale Estate Collective</h3>
  <p>Ferndale means “the home, the house”, buying a property is one of the most expensive expenses and important assets for people. Ferndale is a real estate company located in Gungahlin, Canberra.</p>
  <p>Being a portfolio sales agent and property manager, coupled with our high–profile international real estate experience, Ferndale is considered a market leader on the cutting edge with deep industry knowledge, ranging from landlord–tenant relationships, residential purchases.</p>
</section>

<div class="service" style="left:165px;top:1235px;width:290px;height:290px">
  <svg width="80" height="80" viewBox="0 0 80 80" fill="none" stroke="#222" stroke-width="3"><path d="M10 40 L40 12 L70 40 M18 34 V70 H62 V34"/><rect x="32" y="48" width="16" height="22"/></svg>
  <h4>BUYER</h4>
  <p>Being a portfolio sales agent<br>and property manager, coupled<br>with our high–profile</p>
</div>
<div class="service main" style="left:435px;top:1213px;width:330px;height:330px">
  <svg width="80" height="100" viewBox="0 0 80 100" fill="none" stroke="#fff" stroke-width="3"><path d="M8 4 H56 L72 20 V96 H8 Z"/><path d="M18 24 H46 M18 34 H60"/><path d="M22 66 L40 50 L58 66 M28 62 V84 H52 V62"/></svg>
  <h4>LEASING</h4>
  <p>Being a portfolio sales agent<br>and property manager, coupled<br>with our high–profile</p>
</div>
<div class="service" style="left:745px;top:1235px;width:290px;height:290px">
  <svg width="80" height="80" viewBox="0 0 80 80" fill="none" stroke="#222" stroke-width="3"><path d="M30 30 L52 10 L74 30 V70 H30 Z"/><rect x="44" y="44" width="16" height="26"/><circle cx="18" cy="22" r="10"/></svg>
  <h4>SELLER</h4>
  <p>Being a portfolio sales agent<br>and property manager, coupled<br>with our high–profile</p>
</div>

<section class="abs about">
  <svg class="abs" style="left:0;top:0" width="1200" height="110" viewBox="0 0 1200 110">
    <polygon points="0,0 1200,0 1200,10 600,100 0,10" fill="#fff"/>
    <polyline points="0,10 600,100 1200,10" fill="none" stroke="#1b2538" stroke-width="6"/>
  </svg>
  <div class="about-photo" role="img" aria-label="Modern home interior seen through glass doors"></div>
  <h2>Who is Ferndale?</h2>
  <p style="top:243px">Ferndale means “the home, the house”, buying a property is one of the most expensive expenses and important assets for people. Ferndale is a real estate company located in Gungahlin, Canberra.</p>
  <p style="top:372px">Being a portfolio sales agent and property manager, coupled with our high–profile international real estate experience, Ferndale is considered a market leader on the cutting edge with deep industry knowledge, ranging from landlord–tenant relationships, residential purchases.</p>
  <div class="btn-line">Read More</div>
</section>

<h2 class="abs listings-title">This Month At Ferndale Estate Collective</h2>
<div class="abs tabs"><span class="on">FOR SALE</span><span>FOR LEASE</span><span>OPEN TIMES</span><span>SOLD</span><span>LEASED</span></div>

<article class="card" style="left:111px">
  <div class="photo" role="img" aria-label="Apartment towers with rooftop pool" style="background:linear-gradient(135deg,#8b9aa6,#3b6fb0 60%,#c4a27a)"></div>
  <h5>GUNGAHLIN</h5>
  <div class="addr">Level 5/18 Wattle Grove Avenue</div>
  <dl><dt>Price</dt><dd>$500,000+</dd><dt>Bedrooms</dt><dd>2</dd><dt>Baths</dt><dd>2</dd><dt>Cars</dt><dd>1</dd><dt>Inspection</dt><dd>Sat 21st May 09:40</dd></dl>
  <div class="cta">View Details</div>
</article>
<article class="card" style="left:444px">
  <div class="photo" role="img" aria-label="White modern house with glass frontage" style="background:linear-gradient(160deg,#cfd8de,#f2f2f2 45%,#4d5c3e)"></div>
  <h5>BELCONNEN</h5>
  <div class="addr">172/40 Banksia Street Belconnen</div>
  <dl><dt>Price</dt><dd>$500,000+</dd><dt>Bedrooms</dt><dd>2</dd><dt>Baths</dt><dd>2</dd><dt>Cars</dt><dd>1</dd><dt>Inspection</dt><dd>Sat 21st May 09:40</dd></dl>
  <div class="cta gold">View Details</div>
</article>
<article class="card" style="left:777px">
  <div class="photo" role="img" aria-label="Apartment block with balconies under blue sky" style="background:linear-gradient(160deg,#3e7cc7,#e9e9ee 55%,#b9536b)"></div>
  <h5>GUNGAHLIN</h5>
  <div class="addr">172/40 Banksia Street Belconnen</div>
  <dl><dt>Price</dt><dd>$500,000+</dd><dt>Bedrooms</dt><dd>2</dd><dt>Baths</dt><dd>2</dd><dt>Cars</dt><dd>1</dd><dt>Inspection</dt><dd>Sat 21st May 09:40</dd></dl>
  <div class="cta">View Details</div>
</article>

<section class="abs video" role="img" aria-label="Modern house lit at night">
  <div class="play"><svg width="98" height="98" viewBox="0 0 98 98"><polygon points="40,32 68,49 40,66" fill="#fff"/></svg></div>
  <h2>FERNDALE ESTATE COLLECTIVE</h2>
</section>

<h2 class="abs testi-title">Our Testimonials</h2>
<div class="abs testi-rule"></div>
<article class="testi" style="left:111px">
  <div class="avatar" role="img" aria-label="Client portrait"></div>
  <div class="name">Alex Morgan</div><div class="role">Sed ut perspiciatis unde</div><div class="stars">☆☆☆☆☆</div>
  <div class="quote">”</div>
  <p>Sed ut perspiciatis unde omnis iste natus error sit voluptatem accusantium doloremque laudantium, totam rem aperiam, et qu asi architecto beatae vitae dicta sunt explicabo.</p>
</article>
<article class="testi" style="left:615px">
  <div class="avatar" role="img" aria-label="Client portrait"></div>
  <div class="name">Alex Morgan</div><div class="role">Sed ut perspiciatis unde</div><div class="stars">☆☆☆☆☆</div>
  <div class="quote">”</div>
  <p>Sed ut perspiciatis unde omnis iste natus error sit voluptatem accusantium doloremque laudantium, totam rem aperiam, et qu asi architecto beatae vitae dicta sunt explicabo.</p>
</article>

<footer class="abs footer">
  <svg class="abs" style="left:0;top:0" width="1200" height="368" viewBox="0 0 1200 368">
    <polygon points="0,95 600,2 1200,95 1200,368 0,368" fill="#1b2538"/>
    <polyline points="0,95 600,2 1200,95" fill="none" stroke="#e3b345" stroke-width="5"/>
  </svg>
  <div class="brand"><i></i>Ferndale</div>
  <ul><li>Home</li><li>About Us</li><li>Leasing</li><li>Buy</li><li>Sell</li><li>Our Team</li><li>Blog</li><li>Contact Us</li></ul>
  <div class="social"><span></span><span></span><span></span><span></span></div>
  <div class="copy">Ferndale Estate Collective © 2022.All Rights Reserved.</div>
</footer>

</body>
</html>
```